Business Card Design Project

I have a two letter domain name zu.com.au (lower case font please). I want a business card, cum logo that is die cut (around the zu segment at least) that fits standard business card size.
zu is all about what 'I am' - a journalist, blogger, analyst, commentator. My mantra is "I think therefore zu'.
The reverse of the card only needs my name Olin Verka, email olin@zu.com.au and mobile +61 437 185 923
Mainly people that will use my professional writing services and suppliers that will provide product for review
Business
- One side is zu.com.au (hint - the .com.au can be vertical or horizontal to fit - the zu should be as large as possible).
The other requires large size font name, email and phone details (so no one needs glasses to read it).
The die cut can be just to highlight the zu segment - need not be around the whole card.
Font used in the past was Belwe (old style - very much like the i used in the information symbol).
Colours - no preference - prefer two colour to process colour but can also be an outline font instead of solid colour.

```html
<!DOCTYPE html>
<html lang="en">
<head>
<meta charset="utf-8">
<title>zu.com.au business card</title>
<link href="https://fonts.googleapis.com/css2?family=Ultra&family=Tinos&display=swap" rel="stylesheet">
<style>
  :root {
    --backdrop: #e9e6e1;
    --card: #4a4a4b;
    --card-edge: #3a3a3b;
    --yellow: #fff200;
    --mark-dark: #2e2e2f;
  }
  * { margin: 0; padding: 0; box-sizing: border-box; }
  html, body { width: 1200px; height: 960px; overflow: hidden; }
  body {
    background: var(--backdrop);
    display: flex;
    flex-direction: column;
    align-items: center;
    justify-content: center;
    gap: 56px;
  }
  .card {
    position: relative;
    width: 620px;
    height: 378px;
    background: var(--card);
    border-radius: 18px;
    box-shadow: 0 2px 0 var(--card-edge), 0 14px 30px rgba(0,0,0,0.18);
    overflow: hidden;
  }
  /* front */
  .brand {
    position: absolute;
    left: 88px;
    bottom: 78px;
    display: flex;
    align-items: baseline;
    color: var(--yellow);
    font-family: "Ultra", Georgia, serif;
    line-height: 1;
  }
  .brand-name { font-size: 232px; letter-spacing: -4px; }
  .brand-suffix { font-size: 34px; margin-left: 6px; }
  /* back */
  .holder {
    position: absolute;
    left: 62px;
    top: 52px;
    color: var(--yellow);
    font-family: "Ultra", Georgia, serif;
    font-size: 34px;
    letter-spacing: 1px;
  }
  .contact-list {
    position: absolute;
    left: 50px;
    top: 112px;
    list-style: none;
    font-family: "Tinos", "Times New Roman", serif;
    font-size: 34px;
    color: var(--yellow);
    letter-spacing: 1.5px;
  }
  .contact-item { display: flex; align-items: center; gap: 22px; height: 46px; }
  .contact-icon { width: 20px; height: 20px; flex: none; }
  .back-mark {
    position: absolute;
    left: 62px;
    bottom: 50px;
    font-family: "Ultra", Georgia, serif;
    color: var(--mark-dark);
    display: flex;
    align-items: baseline;
  }
  .back-mark-name { font-size: 30px; }
  .back-mark-suffix { font-size: 14px; margin-left: 2px; }
</style>
</head>
<body>
  <section class="card card-front" aria-label="Card front">
    <div class="brand">
      <span class="brand-name">zu</span><span class="brand-suffix">.com.au</span>
    </div>
  </section>

  <section class="card card-back" aria-label="Card back">
    <h1 class="holder">Olin Verka</h1>
    <ul class="contact-list">
      <li class="contact-item">
        <svg class="contact-icon" viewBox="0 0 20 20" aria-hidden="true">
          <rect x="2" y="5" width="16" height="11" fill="var(--yellow)"/>
          <path d="M2 5 L10 11 L18 5" fill="none" stroke="var(--card)" stroke-width="1.4"/>
        </svg>
        <span>olin@zu.com.au</span>
      </li>
      <li class="contact-item">
        <svg class="contact-icon" viewBox="0 0 20 20" aria-hidden="true">
          <rect x="5" y="2" width="10" height="16" rx="1.5" fill="none" stroke="var(--yellow)" stroke-width="1.8"/>
          <line x1="8.5" y1="15" x2="11.5" y2="15" stroke="var(--yellow)" stroke-width="1.4"/>
        </svg>
        <span>+61 437 185 923</span>
      </li>
    </ul>
    <div class="back-mark">
      <span class="back-mark-name">zu</span><span class="back-mark-suffix">.com.au</span>
    </div>
  </section>
</body>
</html>
```